Marbrook Cupcakes Website

We need a new website. We make Texas-size gourmet cupcakes and cupcake jars. We want a website similar to the one KEYlane is hosting and made. They're charging too much per month. I would like to have Blu Otter host it. see the current site at: marbrookcupcakes.com

```html
<!DOCTYPE html>
<html lang="en">
<head>
<meta charset="utf-8">
<title>Marbrook Cupcakes</title>
<link href="https://fonts.googleapis.com/css2?family=Poppins:wght@400;500;600;700&family=Dancing+Script:wght@600&display=swap" rel="stylesheet">
<style>
:root{
  --brown:#3a1e12;
  --brown-mid:#5a3324;
  --teal:#5cbcc3;
  --teal-dark:#3fa3ab;
  --cream:#f7efe9;
  --pink:#f3e1dc;
  --ink:#222;
  --muted:#555;
  --white:#fff;
  --gold:#f2b630;
}
*{box-sizing:border-box;margin:0;padding:0}
html,body{width:1200px;height:4728px;overflow:hidden}
body{position:relative;background:var(--white);font-family:'Poppins',sans-serif;color:var(--ink)}
.abs{position:absolute}
.script{font-family:'Dancing Script',cursive;color:var(--teal);font-weight:600}
.title{font-family:'Poppins',sans-serif;font-weight:600;color:var(--ink);text-align:center}
.btn{display:inline-flex;align-items:center;gap:8px;border-radius:30px;font-weight:600;font-size:15px}
.btn-teal{background:var(--teal);color:var(--white);padding:12px 26px}
.btn-white{background:var(--white);color:var(--ink);padding:12px 26px}

/* top bar */
.topbar{top:0;left:0;width:1200px;height:40px;background:var(--white);font-size:13px;color:var(--muted);display:flex;align-items:center;padding:0 112px}
.topbar .contact{display:flex;gap:22px;align-items:center}
.topbar .tools{margin-left:auto;display:flex;gap:14px;align-items:center}
.dot-social{width:26px;height:26px;border-radius:50%;background:var(--teal)}
.dot-social.dark{background:var(--brown)}

/* nav */
.nav{top:40px;left:0;width:1200px;height:90px;background:var(--white);border-radius:0 0 40px 40px;z-index:3}
.brand{left:100px;top:8px;width:130px;height:130px;border-radius:50%;background:var(--white);border:4px solid var(--teal);display:flex;align-items:center;justify-content:center;text-align:center;font-weight:600;font-size:16px;color:var(--brown);line-height:1.2}
.menu{left:300px;top:28px;display:flex;gap:34px;font-size:16px;font-weight:500;color:var(--ink)}
.menu .active{color:var(--teal)}
.nav .order{left:930px;top:22px}

/* hero */
.hero{top:120px;left:0;width:1200px;height:620px;background:linear-gradient(90deg,#2a140b 0%,#3a1e12 40%,#6a4330 100%);overflow:hidden}
.hero-photo{right:0;top:0;width:640px;height:620px;background:radial-gradient(circle at 55% 45%,#6b3f2b 0%,#4a2a1b 40%,#2a140b 80%)}
.hero .script{left:210px;top:170px;font-size:34px}
.hero h1{left:140px;top:210px;width:480px;color:var(--white);font-size:46px;line-height:1.15;text-align:center;font-weight:600}
.hero p{left:110px;top:330px;width:520px;color:var(--white);font-size:16px;line-height:1.5}
.hero .btn{left:210px;top:400px}
.dots{left:880px;top:548px;display:flex;gap:14px;align-items:center}
.dots span{width:9px;height:9px;border-radius:50%;background:#c9b6ab}
.dots .on{width:26px;border-radius:6px;background:var(--white)}
.hero-wave{top:640px;left:0;width:1200px;height:160px}

/* section heads */
.head .script{font-size:30px;display:block;text-align:center}
.head .title{font-size:42px;margin-top:-2px}

/* cards */
.card{width:300px;height:480px;border-radius:150px 150px 32px 32px;background:linear-gradient(180deg,#fff 0%,var(--pink) 100%);box-shadow:0 10px 28px rgba(0,0,0,.12);text-align:center}
.card .pic{width:260px;height:260px;border-radius:50%;margin:20px auto 0;border:6px solid var(--white)}
.card h3{font-size:20px;font-weight:600;margin-top:22px}
.card p{font-size:14px;color:var(--muted);line-height:1.55;width:230px;margin:10px auto 0}
.card .plus{position:absolute;left:130px;bottom:-20px;width:40px;height:40px;border-radius:50%;background:var(--white);box-shadow:0 4px 10px rgba(0,0,0,.15);color:var(--teal);font-size:24px;line-height:40px;font-weight:600}
.card.lit .plus{background:var(--teal);color:var(--white)}
.card .price{font-size:18px;font-weight:600;color:var(--teal);margin-top:4px}
.stars{color:var(--gold);font-size:16px;letter-spacing:2px}
.arrow{width:40px;height:40px;display:flex;align-items:center;justify-content:center;font-size:30px;color:var(--muted)}

/* about */
.about-photo{left:-60px;top:1560px;width:620px;height:620px;border-radius:50%;background:radial-gradient(circle at 50% 40%,#9a8a7a 0%,#6a5a4c 55%,#3e342b 100%);border:14px solid var(--white);box-shadow:0 0 0 10px var(--teal)}
.about .script{left:660px;top:1640px;font-size:28px}
.about h2{left:660px;top:1672px;font-size:42px;font-weight:600}
.about p{left:660px;width:480px;font-size:15px;line-height:1.6;color:var(--muted)}
.about .btn{left:660px;top:2056px}
.player{left:940px;top:2030px;width:210px;height:380px;border-radius:100px 100px 40px 40px;background:linear-gradient(180deg,#b8302c 0%,#7a1c1a 60%,#3b1a12 100%);z-index:2}

/* featured */
.featured{top:2220px;left:0;width:1200px;height:760px}
.featured .head .script,.featured .head .title{color:var(--white)}

/* gallery */
.tile{border-radius:6px}

/* testimonials */
.testi-bg{top:3650px;left:0;width:1200px;height:700px;background:linear-gradient(90deg,#f6e9e4 0%,#fff 50%,#e5f4f5 100%)}
.review{width:296px;height:330px;background:var(--white);border-radius:18px;box-shadow:0 10px 26px rgba(0,0,0,.1);text-align:center;padding-top:70px}
.review .avatar{position:absolute;left:108px;top:-40px;width:80px;height:80px;border-radius:50%;background:linear-gradient(135deg,#c89a7a,#7a5a45);border:5px solid var(--white);box-shadow:0 0 0 3px var(--teal)}
.review h4{font-size:16px;font-weight:600;letter-spacing:1px}
.review p{font-size:14px;color:var(--muted);line-height:1.55;width:240px;margin:12px auto 0}

/* footer */
.footer-wave{top:4240px;left:0;width:1200px;height:160px}
.footer{top:4360px;left:0;width:1200px;height:368px;background:var(--brown);color:var(--white)}
.foot-brand{left:110px;top:130px;font-family:'Poppins',sans-serif;font-size:30px;font-weight:600;color:var(--white);display:flex;gap:12px;align-items:center}
.foot-brand i{width:14px;height:14px;border-radius:50%;background:var(--teal);display:block}
.footer h5{font-size:16px;font-weight:600;letter-spacing:1px}
.footer ul{list-style:none;font-size:14px;line-height:2.2;margin-top:12px}
.footer li::before{content:"›";color:var(--teal);margin-right:10px}
.contact-row{display:flex;align-items:center;gap:12px;font-size:13px;margin-top:14px;line-height:1.4}
.contact-row b{width:30px;height:30px;border-radius:50%;background:var(--white);flex:none;display:flex;align-items:center;justify-content:center}
.bottom{left:0;top:310px;width:1200px;height:58px;border-top:1px solid rgba(255,255,255,.2);display:flex;align-items:center;padding:0 110px;font-size:12px}
.pay{width:34px;height:22px;border-radius:3px;background:#e9e2dd;margin-right:6px}
</style>
</head>
<body>

<!-- top bar -->
<div class="abs topbar">
  <div class="contact">
    <span>&#9743; +1 (555) 014 2290</span>
    <span>|</span>
    <span>&#9993; info@marbrookcupcakes.com</span>
  </div>
  <div class="tools">
    <span>&#9906;</span><span>|</span><span>&#128274; LOGIN</span>
    <span class="dot-social"></span><span class="dot-social dark"></span><span class="dot-social dark"></span><span class="dot-social dark"></span>
  </div>
</div>

<!-- hero -->
<section class="abs hero">
  <div class="abs hero-photo" role="img" aria-label="Chocolate cupcake topped with cookie crumbs on a glass stand"></div>
  <span class="abs script">Marbrook Cupcakes</span>
  <h1 class="abs">The Best Cupcake On The Planet</h1>
  <p class="abs">Lorem ipsum dolor sit amet, consectetur adipiscing elit sed do eiusmod incididunt labore.</p>
  <a class="abs btn btn-white">Order Online &#10148;</a>
  <div class="abs dots"><span></span><span></span><span class="on"></span><span></span><span></span></div>
</section>
<svg class="abs hero-wave" viewBox="0 0 1200 160" preserveAspectRatio="none">
  <path d="M0 40 C300 140 700 -10 1200 60 L1200 160 L0 160Z" fill="#fff"/>
  <path d="M0 60 C320 150 720 10 1200 80" fill="none" stroke="#5cbcc3" stroke-width="6"/>
</svg>

<!-- nav -->
<header class="abs nav">
  <div class="abs brand">Marbrook<br>Cupcakes</div>
  <nav class="abs menu"><span class="active">Home</span><span>About Us</span><span>Catering</span><span>Private Events</span><span>Gift Cards</span><span>Press</span></nav>
  <a class="abs btn btn-teal order">Order Online &#10148;</a>
</header>

<!-- collection -->
<div class="abs head" style="top:835px;left:0;width:1200px">
  <span class="script">Shop Marbrook Cupcakes</span>
  <h2 class="title">The Cupcake Collection?</h2>
</div>
<div class="abs arrow" style="left:38px;top:1200px">&#8592;</div>
<div class="abs arrow" style="left:1124px;top:1200px">&#8594;</div>

<div class="abs card" style="left:108px;top:980px">
  <div class="pic" role="img" aria-label="Vanilla cupcake with strawberry on top" style="background:radial-gradient(circle,#e9c7a5,#a0602f)"></div>
  <h3>Lorem Ipsum dolor</h3>
  <p>Lorem ipsum dolor sit amet conse adipiscing elit eiusmod incidi dolor labore.</p>
  <div class="plus">+</div>
</div>
<div class="abs card lit" style="left:450px;top:980px">
  <div class="pic" role="img" aria-label="Cupcake with white frosting" style="background:radial-gradient(circle,#f3efe9,#5cbcc3)"></div>
  <h3>Lorem Ipsum dolor</h3>
  <p>Lorem ipsum dolor sit amet conse adipiscing elit eiusmod incidi dolor labore.</p>
  <div class="plus">+</div>
</div>
<div class="abs card" style="left:792px;top:980px">
  <div class="pic" role="img" aria-label="Cupcakes on glass stands" style="background:radial-gradient(circle,#d8c7b5,#4a3020)"></div>
  <h3>Lorem Ipsum dolor</h3>
  <p>Lorem ipsum dolor sit amet conse adipiscing elit eiusmod incidi dolor labore.</p>
  <div class="plus">+</div>
</div>

<!-- featured band -->
<svg class="abs featured" viewBox="0 0 1200 760" preserveAspectRatio="none">
  <defs><linearGradient id="teal" x1="0" x2="1"><stop offset="0" stop-color="#4fb3ba"/><stop offset="1" stop-color="#6cc8ce"/></linearGradient></defs>
  <path d="M0 80 C400 -10 800 160 1200 60 L1200 620 L0 620Z" fill="url(#teal)"/>
  <path d="M0 60 C400 -30 800 140 1200 40" fill="none" stroke="#cfeef0" stroke-width="5"/>
</svg>

<!-- about -->
<div class="abs about-photo" role="img" aria-label="Shoppers at the cupcake store counter"></div>
<section class="about">
  <span class="abs script">Our Story</span>
  <h2 class="abs">About Us</h2>
  <p class="abs" style="top:1745px">Lorem ipsum dolor sit amet, consectetur adipiscing elit, sed do eiusmod tempor incididunt ut labore et dolore magna aliqua. Ut enim ad minim veniam, quis nostrud exercitation ullamco laboris nisi ut aliquip ex ea commodo consequat. Duis aute irure dolor in reprehenderit in voluptate velit esse cillum dolore.</p>
  <p class="abs" style="top:1920px">Sedu fugiat nulla pariatur excepteur sint occaecat ullamco laboris nisi ut aliquip ex ea commodo consequat. Duis aute irure dolor in reprehen in volu ptate velit esse cillum dolore.</p>
  <a class="abs btn btn-teal">Learn More &#10148;</a>
</section>
<div class="abs player" role="img" aria-label="Basketball player leaping for a dunk"></div>

<div class="abs head" style="top:2335px;left:0;width:1200px">
  <span class="script" style="color:#fff">Shop Marbrook Cupcakes</span>
  <h2 class="title" style="color:#fff">Featured Products</h2>
</div>
<div class="abs arrow" style="left:38px;top:2600px;color:#fff">&#8592;</div>
<div class="abs arrow" style="left:1124px;top:2600px;color:#fff">&#8594;</div>

<div class="abs card" style="left:108px;top:2460px">
  <div class="pic" role="img" aria-label="Chocolate cupcake with cookie on top" style="background:radial-gradient(circle,#c89a6a,#3a1e12)"></div>
  <h3>Lorem Ipsum dolor</h3>
  <p>Lorem ipsum dolor sit amet conse adipiscing elit eiusmod.</p>
  <div class="stars">★★★★★</div><div class="price">$69.99</div>
  <div class="plus">+</div>
</div>
<div class="abs card lit" style="left:450px;top:2460px">
  <div class="pic" role="img" aria-label="Muffin style cupcake on teal backdrop" style="background:radial-gradient(circle,#c9955a,#2f8f96)"></div>
  <h3>Lorem Ipsum dolor</h3>
  <p>Lorem ipsum dolor sit amet conse adipiscing elit eiusmod.</p>
  <div class="stars">★★★★★</div><div class="price">$69.99</div>
  <div class="plus">+</div>
</div>
<div class="abs card" style="left:792px;top:2460px">
  <div class="pic" role="img" aria-label="Cupcake with cream swirl on purple backdrop" style="background:radial-gradient(circle,#f1e3d6,#9a6ad0)"></div>
  <h3>Lorem Ipsum dolor</h3>
  <p>Lorem ipsum dolor sit amet conse adipiscing elit eiusmod.</p>
  <div class="stars">★★★★★</div><div class="price">$69.99</div>
  <div class="plus">+</div>
</div>

<!-- gallery -->
<div class="abs head" style="top:3055px;left:0;width:1200px">
  <span class="script">Our Gallery</span>
  <h2 class="title">Follow #Marbrook Cupcakes</h2>
</div>
<div class="abs tile" style="left:112px;top:3188px;width:250px;height:404px;background:linear-gradient(180deg,#5cbcc3,#e9c98a)" role="img" aria-label="Lemon cupcake on teal background"></div>
<div class="abs tile" style="left:376px;top:3188px;width:212px;height:194px;background:radial-gradient(circle,#b07a45,#5a3420)" role="img" aria-label="Caramel topped cupcakes"></div>
<div class="abs tile" style="left:604px;top:3188px;width:216px;height:194px;background:radial-gradient(circle,#c98a55,#5cbcc3)" role="img" aria-label="Frosted cupcake close-up"></div>
<div class="abs tile" style="left:376px;top:3396px;width:444px;height:196px;background:linear-gradient(90deg,#e8b7b0,#7a4a32,#f0d7c8)" role="img" aria-label="Assorted cupcakes in rows"></div>
<div class="abs tile" style="left:836px;top:3188px;width:252px;height:404px;background:linear-gradient(180deg,#f2e6dc,#9a6548)" role="img" aria-label="Chocolate drizzled cupcake on a stand"></div>

<!-- testimonials -->
<div class="abs testi-bg"></div>
<div class="abs head" style="top:3765px;left:0;width:1200px">
  <span class="script">Testimonials</span>
  <h2 class="title">What Our Customers Say</h2>
</div>
<div class="abs arrow" style="left:38px;top:4030px">&#8249;</div>
<div class="abs" style="left:1124px;top:4030px;width:40px;height:40px;border-radius:50%;background:var(--teal);color:#fff;text-align:center;line-height:38px;font-size:26px">&#8250;</div>

<div class="abs review" style="left:112px;top:3880px">
  <div class="avatar" role="img" aria-label="Customer portrait"></div>
  <h4>— RYAN P</h4><div class="stars">★★★★★</div>
  <p>Lorem ipsum dolor sit amet, conse ctetur adipiscing elit, sed do eiusmod tempor incididunt ut labore et dolore magna aliqua. Ut enim ad minim veniam, quis nostrud sedeo.</p>
</div>
<div class="abs review" style="left:452px;top:3880px">
  <div class="avatar" role="img" aria-label="Customer portrait"></div>
  <h4>— MEGAN T</h4><div class="stars">★★★★★</div>
  <p>Lorem ipsum dolor sit amet, conse ctetur adipiscing elit, sed do eiusmod tempor incididunt ut labore et dolore magna aliqua. Ut enim ad minim veniam, quis nostrud sedeo.</p>
</div>
<div class="abs review" style="left:792px;top:3880px">
  <div class="avatar" role="img" aria-label="Customer portrait"></div>
  <h4>— CARLOS V</h4><div class="stars">★★★★★</div>
  <p>Lorem ipsum dolor sit amet, conse ctetur adipiscing elit, sed do eiusmod tempor incididunt ut labore et dolore magna aliqua. Ut enim ad minim veniam, quis nostrud sedeo.</p>
</div>

<!-- footer -->
<svg class="abs footer-wave" viewBox="0 0 1200 160" preserveAspectRatio="none">
  <path d="M0 60 C300 -10 700 150 1200 40 L1200 160 L0 160Z" fill="#3a1e12"/>
  <path d="M0 40 C300 -30 700 130 1200 20" fill="none" stroke="#5a3324" stroke-width="8"/>
</svg>
<footer class="abs footer">
  <div class="abs foot-brand"><i></i>Marbrook</div>
  <div class="abs" style="left:390px;top:90px">
    <h5>NAVIGATION</h5>
    <ul><li>Home</li><li>About Us</li><li>Catering</li><li>Private Events</li></ul>
  </div>
  <div class="abs" style="left:560px;top:120px">
    <ul><li>Gift Cards</li><li>Press</li><li>Privacy Policy</li><li>Terms Of Conditions</li></ul>
  </div>
  <div class="abs" style="left:745px;top:90px;width:360px">
    <h5>CONTACT US</h5>
    <div class="contact-row"><b style="color:var(--brown)">&#9906;</b><span>2210 Harlow Street, Cedar Plaza, Suite 300, Dallas TX 75201</span></div>
    <div class="contact-row"><b style="color:var(--brown)">&#9993;</b><span>info@marbrookcupcakes.com</span></div>
    <div class="contact-row"><b style="color:var(--brown)">&#9743;</b><span>+1 (555) 014 2290</span></div>
  </div>
  <div class="abs bottom">
    <span class="pay"></span><span class="pay"></span><span class="pay"></span><span class="pay"></span><span class="pay"></span>
    <span style="margin:0 auto">© 2025 ALL RIGHTS RESERVED – MARBROOK CUPCAKES</span>
    <span style="display:flex;gap:8px"><span class="dot-social" style="background:#fff"></span><span class="dot-social" style="background:#fff"></span><span class="dot-social" style="background:#fff"></span><span class="dot-social" style="background:#fff"></span></span>
  </div>
</footer>

</body>
</html>
```